Brightline Energy Product Distribution Brochure

We are looking to have our current brochure for our customers completely redesigned...the idea is to present the relevant information in an attractive way . Our website is brightlineenergyco.example where you can find more information about us. We have included a file with a rough idea of the page order and what each should include but feel free to adapt based on design. The example provided is only for context and doesnt have to be maintained. We will be using the brochure both digitally and in print form. As long as it reads easily and is eye catching, the design can be horizontal or vertical.Final deliverable should be indesign file.

"Our Brands" page: should be limited to one page (space being enough) where it has the header for each one (for example diesel generators) space for one or two lines of text and then the corresponding logos for each of the five categories
Updates

For those asking: the "our brands" page should be a single page layout where there is a header with the corresponding section and space for maybe one line of text followed by the two logos for that category. Each of the product pages should be similar in fashion to the one in the document attached: a photo of the product with some white space and space for the text to be included. We will be posting additional examples today

Target Market(s)

We want to present it to customers both digitally and in print so they can see our products

Industry/Entity Type

Power Generation

Font styles to use
Serif

Requirements
Must have
• Eye catching and able to present the information in a presentable fashion. Rest is up to you.
Nice to have
• Should incorporate the colors of our logo but can also add other depending on design

```html
<!DOCTYPE html>
<html lang="en">
<head>
<meta charset="UTF-8">
<title>Brightline Energy – Distributor Program Guide</title>
<link href="https://fonts.googleapis.com/css2?family=Archivo+Black&family=Work+Sans:wght@400;500;600;700&display=swap" rel="stylesheet">
<style>
  :root {
    --backdrop: #a9a9a9;
    --paper: #ffffff;
    --paper-shade: #f2f2f2;
    --brand-yellow: #fcc521;
    --brand-yellow-deep: #f2b705;
    --ink: #3a3a3a;
    --ink-soft: #6b6b6b;
    --page-w: 510px;
    --page-h: 660px;
  }
  * { box-sizing: border-box; margin: 0; padding: 0; }
  html, body {
    width: 1200px; height: 717px; overflow: hidden;
    background: var(--backdrop);
    font-family: "Work Sans", Arial, sans-serif;
    color: var(--ink);
  }
  .spread {
    position: absolute; left: 90px; top: 28px;
    display: flex;
    box-shadow: 0 18px 40px rgba(0,0,0,.28);
  }
  .page {
    position: relative;
    width: var(--page-w); height: var(--page-h);
    background: var(--paper);
    overflow: hidden;
  }
  .photo { position: absolute; left: 0; width: 100%; }

  /* Back cover */
  .back-cover .intro { position: absolute; left: 44px; top: 42px; width: 420px; }
  .intro-title {
    font-family: "Archivo Black", Arial, sans-serif;
    font-size: 21px; letter-spacing: .5px; color: var(--ink);
  }
  .accent-rule { display: block; width: 48px; height: 3px; background: var(--brand-yellow); margin: 6px 0 10px; }
  .intro-text { font-size: 9.5px; line-height: 1.35; color: var(--ink-soft); }
  .back-cover .photo {
    top: 150px; height: 330px;
    background:
      radial-gradient(ellipse at 5% 95%, rgba(255,120,40,.85), rgba(255,140,60,0) 55%),
      linear-gradient(160deg, #5b7fa8 0%, #9fb7cf 35%, #4e6d92 60%, #2c3f5a 100%);
  }
  .back-cover .footer-band { position: absolute; left: 0; top: 480px; width: 100%; height: 180px; }
  .yellow-wedge { position: absolute; right: 0; top: 0; }
  .brand-lockup {
    position: absolute; display: flex; align-items: center; gap: 10px;
    font-size: 20px; font-weight: 500; color: var(--ink); letter-spacing: .5px;
  }
  .brand-mark { width: 22px; height: 22px; background: var(--brand-yellow); }
  .back-cover .brand-lockup { left: 44px; top: 92px; }
  .company-address { position: absolute; left: 258px; top: 40px; font-size: 10.5px; line-height: 1.35; color: var(--ink); }
  .company-address .phone { font-weight: 700; margin-top: 2px; }
  .company-address .web { font-weight: 700; color: var(--brand-yellow-deep); margin-top: 14px; }

  /* Front cover */
  .front-cover .title-block { position: absolute; left: 46px; top: 34px; }
  .cover-title {
    font-family: "Archivo Black", Arial, sans-serif;
    font-size: 21px; line-height: 1.05; letter-spacing: .5px; color: var(--ink);
  }
  .front-cover .accent-rule { width: 44px; margin: 10px 0 8px; }
  .cover-subtitle { font-size: 12.5px; font-weight: 600; letter-spacing: 1px; line-height: 1.2; color: var(--ink); }
  .title-accent { position: absolute; right: 0; top: 0; width: 230px; height: 130px; background: var(--brand-yellow); }
  .front-cover .photo {
    top: 130px; height: 315px;
    background:
      radial-gradient(ellipse at 85% 60%, rgba(255,190,60,.85), rgba(255,170,40,0) 45%),
      radial-gradient(ellipse at 40% 75%, rgba(240,150,40,.6), rgba(240,150,40,0) 50%),
      linear-gradient(180deg, #3d4f6a 0%, #2a2f3c 55%, #5a3f24 100%);
  }
  .contact-panel {
    position: absolute; left: 0; top: 445px; width: 250px; height: 215px;
    background: var(--brand-yellow); padding: 112px 0 0 50px;
  }
  .contact-phone { font-size: 13px; font-weight: 700; color: var(--ink); }
  .contact-web { font-size: 9px; margin-top: 12px; color: var(--ink); }
  .front-cover .brand-lockup { left: 290px; top: 575px; font-size: 19px; }
</style>
</head>
<body>
  <main class="spread">
    <section class="page back-cover">
      <div class="intro">
        <h2 class="intro-title">LOREM IPSUM</h2>
        <span class="accent-rule"></span>
        <p class="intro-text">Lorem ipsum dolor sit amet, consectetuer adipiscing elit, sed diam nonummy nibh euismod tincidunt ut laoreet dolore magna aliquam erat volutpat. Ut wisi enim ad minim veniam, quis nostrud exerci tation ullamcorper suscipit lobortis nisl ut aliquip ex ea commodo consequat. Duis autem vel eum iriure dolor in hendrerit in vulputate velit esse molestie consequat.</p>
      </div>
      <div class="photo" role="img" aria-label="Industrial plant interior with large steel pipework and warm sunlight"></div>
      <div class="footer-band">
        <svg class="yellow-wedge" width="160" height="180" viewBox="0 0 160 180" aria-hidden="true">
          <polygon points="0,0 160,0 160,180 110,180" fill="var(--brand-yellow)"/>
        </svg>
        <div class="brand-lockup"><span class="brand-mark"></span>Brightline Energy</div>
        <address class="company-address">
          Brightline Energy Ltd.<br>4410 Harbor Road<br>Dayton, OH 45402, USA
          <div class="phone">1-800-555-0142</div>
          <div class="web">brightlineenergyco.example</div>
        </address>
      </div>
    </section>

    <section class="page front-cover">
      <div class="title-accent"></div>
      <header class="title-block">
        <h1 class="cover-title">DISTRIBUTOR<br>PROGRAM GUIDE</h1>
        <span class="accent-rule"></span>
        <p class="cover-subtitle">DIESEL GENERATORS<br>ALTERNATORS &amp; PARTS</p>
      </header>
      <div class="photo" role="img" aria-label="Industrial power plant illuminated at dusk"></div>
      <div class="contact-panel">
        <div class="contact-phone">1-800-555-0142</div>
        <div class="contact-web">brightlineenergyco.example</div>
      </div>
      <div class="brand-lockup"><span class="brand-mark"></span>Brightline Energy</div>
    </section>
  </main>
</body>
</html>
```